Chai Tea Company needs a Tea Packaging Box Design

Tea Packaging
Dimensions of the Tea Packaging Box: Height 13 cm; Width 8.5 cm; Depth 7 cm
Individual Teabag Packet/ Sachet: Width 6.5 cm; Length 8.25 cm
We are looking for a new tea packaging design, for our tea business. The material of the box is cardboard. We are also looking for a design that will be on each individual tea bag sachet/packet that goes into the box. This design will be very similar to what you design for the tea packaging box.
Product Info:
Our tea company is called “Velmora Brew”. We sell two types of Chai Tea, once called “Velmora Gold” and one called “Velmora Meadow”. The Velmora Gold has caffeine, while the Velmora Meadow is Naturally Caffeine Free. The Velmora Gold has a black tea base, while the Velmora Meadow has a Rooibos tea base. We will need two tea packaging designs, one for each Chai Tea flavour. The designs for both the teas can be similar, but make sure that you can easily distinguish one from the other (example: make them have different colours or pictures). Both the chai teas, come from the same product line.
Tea Packaging Design:
We are looking for high end tea packaging. We produce high quality teas, and we would like to portray this in our tea packaging. Our teas are made with no artificial flavourings, natural flavourings, or preservatives, so we would also like a natural, organic, high quality look to our tea packaging. Our current logo is a llama. It would be great if you could make the current logo more polished and well made. If you feel that the llama is not well suited or you would like to design the llama differently, we are open to your creative ideas.
General Basic Info:
Keep in mind, we will have both English and French writing on the tea packaging. You do not need to worry about the French writing (we will do the translation), just make sure there is room for it. However, if you feel that you are capable and knowledgeable of incorporating both French and English language into the tea packaging that would be of great help and value.
Back of the Box:
- Will have ingredients and brewing instructions. Basic brewing instructions are: “Add hot water to teabag. Steep for 5-7 minutes, depending on strength preferred. Add milk and your choice of sweetener. Enjoy! See inside panel of box for more detailed instructions”. (The basic brewing instructions, can further be polished or written in a more creative or professional manner).
Front of the Box:
- Will have company name, type of tea, little description of the tea
- 18 teabags
- 54 g (1.9 OZ)
- Should state that this is a product of Alberta, Canada.
Side of the Box:
Any creative wording, slogan, or description about the tea, or whatever you feel would be good on the side of the box.
On the inside flap of the side of the box, there will be detailed instructions on how to brew the tea. These will be different from the simplified brewing instructions on the back of the box. I have attached the advanced brewing instructions as a file. These instructions can further be simplified or reduced to make it easier and cleaner for the consumers to read.
Individual Tea Sachets/ Packets
- These will have a matching look and design of the tea box packaging, except on a smaller scale. Each individual sachet will have the company name, type of tea, little description of the tea in the front of the sachet, while the back will contain the ingredients, and basic brewing instructions.
I have attached a few files, with the dimensions, ingredients, detailed brewing directions, and current logo of the business.
If you have any questions, about the design or packaging please let me know. The winning designer will be required to do a few additional tweaks to finalize the product. Thank you for your time and happy designing!

```html
<!DOCTYPE html>
<html lang="en">
<head>
<meta charset="utf-8">
<title>Velmora Meadow – Tea Box Dieline</title>
<link rel="stylesheet" href="https://fonts.googleapis.com/css2?family=Cinzel:wght@400;700&family=Playball&display=swap">
<style>
:root{
  --maroon:#5a0d12;
  --beige:#bfa77a;
  --paper:#f4f2ee;
  --rose:#b5605a;
  --ink:#3a2a26;
  --line:#b9b9b9;
  --gold:#d9a53a;
  --leaf:#6a9a52;
}
*{box-sizing:border-box;margin:0;padding:0}
html,body{width:1200px;height:778px;overflow:hidden;background:#fff}
.canvas{position:relative;width:1200px;height:778px;font-family:"Cinzel",serif;color:var(--ink)}
.abs{position:absolute}
.dieline{position:absolute;left:0;top:0}
.brand{font-family:"Cinzel",serif;font-weight:700;color:var(--ink);letter-spacing:.5px;text-align:center;white-space:nowrap;line-height:1.1}
.variety{font-family:"Playball",cursive;color:var(--rose);text-align:center;white-space:nowrap;line-height:1.2}
.small{font-size:5.5px;line-height:1.4;text-align:center;text-transform:uppercase}
.head{color:var(--rose);font-weight:700;font-size:6px;line-height:1.4;text-align:center;text-transform:uppercase}
.mark{background:linear-gradient(180deg,#c88a84,#a9504a);border-radius:4px}
.tea-tags{display:flex;justify-content:center;gap:6px;font-size:6px;line-height:1.2;color:var(--rose);text-transform:uppercase;text-align:center}
.tea-tags small{display:block;font-size:4px;color:var(--ink)}
.left{text-align:left}
/* sachet */
.sachet{left:55px;top:255px;width:195px;height:393px;background:var(--paper)}
.sachet .band-l{left:0;top:0;width:27px;height:100%;background:var(--maroon)}
.sachet .band-r{right:0;top:0;width:45px;height:100%;background:var(--maroon)}
.sachet .face{left:29px;width:119px}
.sachet .fold{left:35px;top:200px;width:105px;border-top:1px dashed #999}
.sachet .back{top:204px;height:180px;display:flex;flex-direction:column;justify-content:flex-end;transform:rotate(180deg)}
.tear{left:50px;top:272px;width:200px;border-top:1px dashed #222}
.tear-label{left:87px;top:265px;font-size:5px}
/* box panels */
.back-label{left:362px;top:225px;width:143px;height:260px;background:#fff;padding:10px 10px 0}
.front-label{left:752px;top:225px;width:136px;height:260px;background:var(--paper);padding-top:8px}
.lid-label{left:908px;top:45px;width:202px;height:180px;background:var(--paper)}
.lid-seal{left:12px;top:40px;width:92px;height:92px;border-radius:50%;background:var(--gold);border:5px solid var(--maroon)}
.lid-brand{left:128px;top:32px;font-size:15px;writing-mode:vertical-rl}
.lid-mark{left:152px;top:50px;width:44px;height:62px}
</style>
</head>
<body>
<div class="canvas">

  <svg class="dieline" width="1200" height="778" viewBox="0 0 1200 778">
    <g fill="#fff" stroke="var(--line)" stroke-width="1">
      <path d="M348 225 V140 Q348 135 353 135 H505 Q510 135 510 140 V215 H520 V225 Z"/>
      <path d="M730 225 V215 H736 V140 Q736 135 741 135 H900 Q905 135 905 140 V225 Z"/>
      <path d="M348 485 V575 H515 V485 Z"/>
      <path d="M520 485 V680 Q520 685 525 685 H725 Q730 685 730 680 V485 Z"/>
      <path d="M730 485 V575 H905 V485 Z"/>
      <path d="M908 225 V30 Q908 25 913 25 H1110 Q1115 25 1115 30 V225 Z"/>
      <path d="M1110 225 L1138 245 V470 L1110 485 Z"/>
      <rect x="348" y="225" width="762" height="260"/>
    </g>
    <rect x="348" y="225" width="14" height="260" fill="var(--beige)"/>
    <rect x="505" y="225" width="15" height="260" fill="var(--beige)"/>
    <rect x="520" y="225" width="210" height="260" fill="var(--maroon)"/>
    <polygon points="520,225 710,485 520,485" fill="var(--beige)"/>
    <rect x="730" y="225" width="180" height="260" fill="var(--beige)"/>
    <rect x="910" y="225" width="200" height="260" fill="var(--maroon)"/>
    <polygon points="1110,230 1110,485 912,485" fill="var(--beige)"/>
    <rect x="520" y="485" width="210" height="30" fill="var(--beige)"/>
    <rect x="520" y="640" width="210" height="25" fill="var(--beige)"/>
    <path d="M908 45 V30 Q908 25 913 25 H1110 Q1115 25 1115 30 V45 Z" fill="var(--maroon)"/>
    <g stroke="#fff" stroke-dasharray="4 3" stroke-width=".8" fill="none" opacity=".8">
      <line x1="348" y1="225" x2="1110" y2="225"/>
      <line x1="348" y1="485" x2="1110" y2="485"/>
    </g>
  </svg>

  <!-- Sachet -->
  <div class="abs sachet">
    <div class="abs band-l"></div>
    <div class="abs band-r"></div>
    <div class="abs face" style="top:28px">
      <div class="mark" role="img" aria-label="Llama illustration" style="width:56px;height:56px;margin:0 auto"></div>
      <div class="brand" style="font-size:12px;margin-top:3px">VELMORA BREW</div>
      <div class="tea-tags" style="margin-top:7px"><span>Chai Tea<small>Caffeine free</small></span><span>■</span><span>Thé Chai<small>Sans caféine</small></span></div>
      <div class="variety" style="font-size:15px;margin-top:3px">Velmora Meadow</div>
      <div class="small" style="color:var(--rose);font-size:4.6px">A rich blend of South African rooibos tea, cardamom, fennel, cloves, ginger and cinnamon</div>
      <div class="small" style="color:var(--rose);font-size:3.6px;margin-top:2px">Un riche mélange de rooibos sud-africain, cardamome, fenouil, clous de girofle, gingembre et cannelle</div>
      <div class="small" style="color:var(--rose);font-size:7px;margin-top:2px">One tea bag</div>
    </div>
    <div class="abs fold"></div>
    <div class="abs face back">
      <div class="head">Directions</div>
      <div class="small" style="font-size:4.6px">To get the most out of every cup, bring water to boiling and steep 5 to 7 minutes depending on strength preferred</div>
      <div class="small" style="font-size:4.6px;margin-top:3px">For a stronger tea, use 2 tea bags</div>
      <div class="small" style="font-size:4.6px;margin-top:3px">Add milk and your choice of sweetener. Enjoy!</div>
      <div class="small" style="font-size:4.6px">*See inside panel of box for more detailed instructions</div>
      <div class="head" style="margin-top:7px">Ingredients</div>
      <div class="small" style="font-size:4.6px">Rooibos tea, cardamom, cloves,<br>fennel, ginger, and cinnamon</div>
      <div class="small" style="font-weight:700;font-size:6px;margin-top:9px">Not for individual resale</div>
      <div class="brand" style="font-size:11px;margin-top:9px">VELMORA BREW</div>
      <div class="small" style="font-size:4.4px;margin-top:3px">Box 1200 RPO Northgate<br>Red Deer, Alberta<br>Canada</div>
    </div>
  </div>
  <div class="abs tear"></div>
  <div class="abs tear-label">Please Tear Here</div>

  <!-- Back panel -->
  <div class="abs back-label">
    <div class="head">Directions</div>
    <div class="small left" style="margin-top:4px">To get the most out of every cup, bring water to boiling and steep 5 to 7 minutes depending on strength preferred.</div>
    <div class="small left" style="margin-top:6px">For a stronger tea, use 2 tea bags.</div>
    <div class="small left" style="margin-top:6px">Add milk and your choice of sweetener. Enjoy!</div>
    <div class="small" style="margin-top:4px">*See inside panel of box for more detailed instructions</div>
    <div class="head" style="margin-top:10px">Ingredients</div>
    <div class="small" style="margin-top:3px">Rooibos tea, cardamom, cloves,<br>fennel, ginger, and cinnamon</div>
    <div class="mark" role="img" aria-label="Llama illustration" style="width:46px;height:52px;margin:14px auto 0"></div>
    <div class="brand" style="font-size:12px;margin-top:3px">VELMORA BREW</div>
    <div class="small" style="margin-top:12px">Box 1200 RPO Northgate<br>Red Deer, Alberta<br>Canada</div>
    <div style="width:12px;height:12px;border-radius:50%;background:var(--leaf);margin:6px auto 0"></div>
  </div>

  <!-- Front panel -->
  <div class="abs front-label">
    <div class="tea-tags"><span>Chai Tea<small>Caffeine free</small></span><span>■</span><span>Thé Chai<small>Sans caféine</small></span></div>
    <div class="variety" style="font-size:18px;margin-top:3px">Velmora Meadow</div>
    <div class="small" style="color:var(--rose);font-size:4.8px;padding:0 6px">A rich blend of South African rooibos tea, cardamom, fennel, cloves, ginger and cinnamon</div>
    <div style="height:1px;background:var(--rose);margin:3px 8px"></div>
    <div class="small" style="color:var(--rose);font-size:3.6px;padding:0 6px">Un riche mélange de rooibos sud-africain, cardamome, fenouil, clous de girofle, gingembre et cannelle</div>
    <div class="mark" role="img" aria-label="Llama illustration" style="width:80px;height:80px;margin:5px auto 0"></div>
    <div class="brand" style="font-size:13px;margin-top:3px">VELMORA BREW</div>
    <div style="text-align:center;color:var(--rose);font-size:17px;line-height:1;margin-top:5px">18</div>
    <div class="small" style="color:var(--rose);font-size:6.5px;line-height:1.2">Tea bags</div>
    <div class="small" style="color:var(--rose);font-size:3.8px">Sachets de thé</div>
    <div class="small" style="color:var(--rose);font-size:5.5px;line-height:1.3;margin-top:1px">Net Wt 54 g (1.9 oz)</div>
    <div class="small" style="color:var(--rose);font-size:3.8px">Product of Alberta, Canada</div>
  </div>

  <!-- Lid -->
  <div class="abs lid-label">
    <div class="abs lid-seal" role="img" aria-label="Natural product seal"></div>
    <div class="abs brand lid-brand">VELMORA BREW</div>
    <div class="abs mark lid-mark" role="img" aria-label="Llama illustration"></div>
  </div>

</div>
</body>
</html>
```